Resident Guide for Senior Living Community

I need to create an informational magazine for residents that live in an Assisted Living community. This magazine is designed to educate the resident about the different service options and features that the community provides. I don't want to use any of the pictures in the Word Document - please use the uploaded picture instead. The final design should be both informational and elegant. The text in the word document is the actual text that needs to be used in the Resident Guide. Thanks!

Target Market(s)

Senior citizens and adult children (55 - 65 years old)

Industry/Entity Type

Assisted Living

Requirements
Must have
• Must be elegant - think Velmont Hargrove. Needs to have a lot of pictures and the logo must be used. The logo is the Plaque that says The Birch Lodge.
Nice to have
• The Word doucment is the old Resident Guide - we are looking for a refresh using the same content.
Should not have
• please do not use any pictures from the Word Document other than the Logo.

```html
<!DOCTYPE html>
<html lang="en">
<head>
<meta charset="UTF-8">
<title>Resident Guide – Table of Contents</title>
<link href="https://fonts.googleapis.com/css2?family=Crimson+Pro:wght@400&family=Libre+Bodoni:ital,wght@1,600&display=swap" rel="stylesheet">
<style>
  :root {
    --paper: #ffffff;
    --ink: #1c1c1c;
    --gold: #e3cf5e;
    --gold-soft: #ecdd8d;
  }
  * { margin: 0; padding: 0; box-sizing: border-box; }
  html, body {
    width: 1200px;
    height: 777px;
    overflow: hidden;
    background: var(--paper);
  }
  .spread {
    position: relative;
    width: 1200px;
    height: 777px;
    background: var(--paper);
  }
  .contents-frame {
    position: absolute;
    left: 670px;
    top: 70px;
    width: 464px;
    height: 636px;
    border: 2px solid var(--gold);
  }
  .contents-frame::after {
    content: "";
    position: absolute;
    inset: 2px;
    border: 1px solid var(--gold-soft);
  }
  .contents-title {
    position: absolute;
    top: 35px;
    left: 0;
    right: 0;
    text-align: center;
    font-family: "Libre Bodoni", "Bodoni Moda", serif;
    font-style: italic;
    font-weight: 600;
    font-size: 16px;
    letter-spacing: -0.2px;
    color: var(--ink);
  }
  .contents-list {
    position: absolute;
    top: 73px;
    left: 44px;
    width: 384px;
    list-style: none;
    font-family: "Crimson Pro", "Times New Roman", serif;
    font-size: 14.2px;
    line-height: 16.5px;
    color: var(--ink);
  }
  .contents-entry {
    display: flex;
    align-items: baseline;
  }
  .entry-title { white-space: nowrap; }
  .entry-leader {
    flex: 1;
    height: 4px;
    margin: 0 1px 0 3px;
    background-image: radial-gradient(circle, var(--ink) 0.55px, transparent 0.85px);
    background-size: 3px 3px;
    background-repeat: repeat-x;
    background-position: left bottom;
  }
  .entry-page { white-space: nowrap; }
</style>
</head>
<body>
  <main class="spread">
    <section class="contents-frame">
      <h1 class="contents-title">Table of Contents</h1>
      <ol class="contents-list">
        <li class="contents-entry"><span class="entry-title">Our Family Pledg</span><span class="entry-leader"></span><span class="entry-page">2</span></li>
        <li class="contents-entry"><span class="entry-title">Letter from the Founder and CEO</span><span class="entry-leader"></span><span class="entry-page">3</span></li>
        <li class="contents-entry"><span class="entry-title">“Golden Hearth” Service and Care</span><span class="entry-leader"></span><span class="entry-page">6</span></li>
        <li class="contents-entry"><span class="entry-title">Special Services</span><span class="entry-leader"></span><span class="entry-page">10</span></li>
        <li class="contents-entry"><span class="entry-title">Service Levels and Fees – Willow Springs</span><span class="entry-leader"></span><span class="entry-page">12</span></li>
        <li class="contents-entry"><span class="entry-title">Service Levels &amp; Fees – Ashford</span><span class="entry-leader"></span><span class="entry-page">14</span></li>
        <li class="contents-entry"><span class="entry-title">Respite Care</span><span class="entry-leader"></span><span class="entry-page">15</span></li>
        <li class="contents-entry"><span class="entry-title">All Levels of Healtcare Include</span><span class="entry-leader"></span><span class="entry-page">16</span></li>
        <li class="contents-entry"><span class="entry-title">Our Heritage.</span><span class="entry-leader"></span><span class="entry-page">17</span></li>
      </ol>
    </section>
  </main>
</body>
</html>
```